Website update for Harborline Ledger Partners & Bookkeeping

Our website needs updating
www.harborlineledgerpartners.com
Here are some of our latest print pieces to use as a guide?
I have also attached our graphic identity guide which includes the Pantone colors

Target Market(s)

Insurance Agencies

Industry/Entity Type

Accounting

Number of Pages Required

5+ page

```html
<!DOCTYPE html>
<html lang="en">
<head>
<meta charset="utf-8">
<title>Harborline Ledger Partners &amp; Bookkeeping</title>
<link href="https://fonts.googleapis.com/css2?family=Open+Sans:wght@400;600;700&family=Raleway:wght@500;600;700&display=swap" rel="stylesheet">
<style>
:root{
  --teal:#1fa597;
  --teal-dark:#168a7e;
  --slate:#5b6062;
  --ink:#3a3f41;
  --muted:#8a8f91;
  --band:#eeeff0;
  --footer:#2f3234;
  --white:#ffffff;
  --line:#dcdfe0;
}
*{box-sizing:border-box;margin:0;padding:0}
html,body{width:885px;height:1200px;overflow:hidden;background:var(--white)}
body{font-family:"Open Sans",Arial,sans-serif;color:var(--ink);position:relative}
.wrap{width:590px;margin:0 auto;position:relative}

.site-header{height:80px}
.site-header .wrap{display:flex;justify-content:space-between;align-items:center;height:80px}
.brand{display:flex;align-items:center;gap:10px}
.brand-mark{width:30px;height:30px;background:var(--teal);flex-shrink:0}
.brand-name{font-family:"Raleway",sans-serif;font-weight:700;font-size:15px;color:var(--slate);line-height:1.15;width:210px}
.call{text-align:right}
.call small{display:block;font-size:9px;font-weight:700;color:var(--teal);letter-spacing:1px}
.call strong{display:flex;align-items:center;gap:5px;font-size:18px;color:var(--teal);font-weight:700;white-space:nowrap}

.main-nav{background:var(--teal);height:30px}
.main-nav ul{list-style:none;display:flex;justify-content:space-between;height:30px;width:590px;margin:0 auto}
.main-nav li{font-size:9px;font-weight:600;color:var(--white);padding:0 12px;line-height:30px;letter-spacing:.4px;white-space:nowrap}
.main-nav li.active{background:var(--teal-dark)}

.hero{height:300px;position:relative;background:linear-gradient(120deg,#c9d3d8 0%,#e7ecee 45%,#b9c4ca 100%)}
.hero h1{position:absolute;top:110px;left:0;right:0;text-align:center;font-family:"Raleway",sans-serif;font-weight:600;font-size:25px;color:var(--white);line-height:1.3;text-shadow:0 1px 3px rgba(0,0,0,.35)}
.hero .arrow{position:absolute;top:120px}
.hero .arrow.prev{left:150px}.hero .arrow.next{right:150px}

.services{position:relative;margin-top:-50px;display:flex;gap:6px;width:560px;margin-left:auto;margin-right:auto}
.service{flex:1;height:190px;color:var(--white);text-align:center;padding:16px 14px}
.service.teal{background:var(--teal)}
.service.gray{background:var(--slate)}
.service .icon{width:34px;height:34px;margin:0 auto 12px;background:var(--white);border-radius:3px;display:flex;align-items:center;justify-content:center}
.service h3{font-family:"Raleway",sans-serif;font-size:14px;font-weight:600;margin-bottom:8px;white-space:nowrap}
.service p{font-size:8.5px;line-height:1.5;opacity:.9;margin-bottom:10px}
.btn-ghost{display:inline-block;border:1px solid var(--white);font-size:7.5px;font-weight:700;padding:4px 10px;letter-spacing:.5px}

.intro{display:flex;justify-content:space-between;margin-top:28px}
.intro-text{width:370px}
.intro-text h2{font-family:"Raleway",sans-serif;font-size:19px;font-weight:600;color:var(--ink);line-height:1.2}
.intro-text h2 span{display:block;font-size:13px;font-weight:500;color:var(--muted);margin-top:3px}
.intro-text .lead{font-size:9px;font-weight:700;margin:12px 0 6px}
.intro-text p{font-size:9px;line-height:1.6;color:var(--muted)}
.quote{width:180px;border:1px solid var(--line);padding:12px}
.quote h4{font-family:"Raleway",sans-serif;color:var(--teal);font-size:13px;font-weight:600;margin-bottom:10px}
.quote .field{height:18px;border:1px solid var(--line);margin-bottom:6px;font-size:7.5px;color:var(--muted);padding:3px 5px}
.btn-solid{display:inline-block;background:var(--teal);color:var(--white);font-size:7.5px;font-weight:700;padding:5px 12px;letter-spacing:.5px;white-space:nowrap}

.how{background:var(--band);margin-top:28px;height:350px;padding-top:22px}
.how .wrap{display:flex;justify-content:space-between}
.how-col{width:360px}
.section-title{font-family:"Raleway",sans-serif;font-size:15px;font-weight:600;color:var(--teal);margin-bottom:12px}
.how-row{display:flex;gap:12px}
.how-photo{width:150px;height:110px;flex-shrink:0;background:linear-gradient(135deg,#b7c2c7,#dfe4e6)}
.how-body h5{font-size:10px;color:var(--teal);margin-bottom:5px}
.how-body p{font-size:8.5px;line-height:1.6;color:var(--muted);margin-bottom:10px}
.blogs{width:190px}
.blogs h4{font-family:"Raleway",sans-serif;font-size:15px;font-weight:600;color:var(--ink);margin-bottom:12px}
.post{margin-bottom:10px}
.post h6{font-size:8.5px;color:var(--teal);font-weight:600}
.post p{font-size:8px;color:var(--muted);line-height:1.5}

.site-footer{position:absolute;left:0;right:0;bottom:0;height:70px;background:var(--footer);color:#c6cacc}
.site-footer .wrap{display:flex;justify-content:space-between;padding-top:18px}
.site-footer ul{list-style:none;display:flex;gap:14px;font-size:8px;font-weight:600;color:var(--white)}
.site-footer .copy{font-size:7.5px;margin-top:10px}
.site-footer address{font-style:normal;font-size:8px;text-align:right;line-height:1.6}
</style>
</head>
<body>
<header class="site-header">
  <div class="wrap">
    <div class="brand">
      <span class="brand-mark"></span>
      <span class="brand-name">Harborline Ledger Partners &amp; Bookkeeping</span>
    </div>
    <div class="call">
      <small>CALL US TODAY</small>
      <strong><svg width="14" height="14" viewBox="0 0 24 24"><path fill="#1fa597" d="M6.6 10.8a15 15 0 006.6 6.6l2.2-2.2a1 1 0 011-.25 11.4 11.4 0 003.6.6 1 1 0 011 1V20a1 1 0 01-1 1A17 17 0 013 4a1 1 0 011-1h3.5a1 1 0 011 1 11.4 11.4 0 00.6 3.6 1 1 0 01-.25 1z"/></svg>860.555.0142</strong>
    </div>
  </div>
</header>

<nav class="main-nav">
  <ul>
    <li class="active">HOME</li><li>ABOUT US</li><li>TRAINING</li><li>OUR SERVICES</li><li>HOW IT WORKS</li><li>RESOURCES</li><li>BLOG</li><li>CONTACT</li>
  </ul>
</nav>

<section class="hero" role="img" aria-label="Photo of accountants reviewing paperwork with a client">
  <svg class="arrow prev" width="16" height="34" viewBox="0 0 16 34"><path d="M14 2L2 17l12 15" fill="none" stroke="#fff" stroke-width="2"/></svg>
  <h1>Need help with your insurance agency's<br>Accounting and Bookkeeping</h1>
  <svg class="arrow next" width="16" height="34" viewBox="0 0 16 34"><path d="M2 2l12 15L2 32" fill="none" stroke="#fff" stroke-width="2"/></svg>
</section>

<section class="services">
  <article class="service teal">
    <div class="icon"><svg width="18" height="18" viewBox="0 0 24 24"><text x="12" y="18" text-anchor="middle" font-size="18" font-weight="700" fill="#1fa597" font-family="Open Sans,sans-serif">$</text></svg></div>
    <h3>Bookkeeping</h3>
    <p>Accurate monthly records kept for your agency so you always know where you stand.</p>
    <span class="btn-ghost">READ MORE</span>
  </article>
  <article class="service gray">
    <div class="icon"><svg width="18" height="18" viewBox="0 0 24 24"><path d="M4 20h16M6 17v-5M11 17V8M16 17v-7M20 17V5" stroke="#5b6062" stroke-width="2.4" fill="none"/></svg></div>
    <h3>Financial Statements</h3>
    <p>Clear statements prepared each month to track income, expenses and growth.</p>
    <span class="btn-ghost">READ MORE</span>
  </article>
  <article class="service teal">
    <div class="icon"><svg width="18" height="18" viewBox="0 0 24 24"><rect x="5" y="3" width="14" height="18" rx="1.5" fill="none" stroke="#1fa597" stroke-width="2"/><rect x="8" y="6" width="8" height="3" fill="#1fa597"/><path d="M8 13h2M12 13h2M8 17h2M12 17h2" stroke="#1fa597" stroke-width="2"/></svg></div>
    <h3>Accounting Service</h3>
    <p>Full service accounting built around the way insurance agencies work.</p>
    <span class="btn-ghost">READ MORE</span>
  </article>
</section>

<section class="wrap intro">
  <div class="intro-text">
    <h2>Experienced team of insurance agency<span>bookkeeping professionals maintaining your books</span></h2>
    <p class="lead">Affordable, professional services for less than the cost of an in-house bookkeeper</p>
    <p>We handle reconciliations, commissions, payroll and reporting so your team can focus on clients. Our specialists understand carrier statements, agency cash flow and the details that keep your books clean and ready for review at any time.</p>
  </div>
  <aside class="quote">
    <h4>Get a Quote</h4>
    <div class="field">Name</div>
    <div class="field">Email</div>
    <div class="field">Phone</div>
    <div class="field">Message</div>
    <span class="btn-solid">SUBSCRIBE</span>
  </aside>
</section>

<section class="how">
  <div class="wrap">
    <div class="how-col">
      <h3 class="section-title">How it works</h3>
      <div class="how-row">
        <div class="how-photo" role="img" aria-label="Photo of an advisor meeting with an agency owner"></div>
        <div class="how-body">
          <h5>Onboarding made simple</h5>
          <p>We review your current books, set up secure access and build a monthly routine that fits your agency. You receive clear reports and a dedicated contact.</p>
          <span class="btn-solid">READ MORE</span>
        </div>
      </div>
    </div>
    <div class="blogs">
      <h4>Recent Blogs</h4>
      <div class="post"><h6>Year-end checklist for agencies</h6><p>Steps to close the books cleanly before tax season.</p></div>
      <div class="post"><h6>Tracking carrier commissions</h6><p>Simple ways to reconcile statements each month.</p></div>
      <div class="post"><h6>Payroll tips for small agencies</h6><p>Avoid common errors when paying producers.</p></div>
    </div>
  </div>
</section>

<footer class="site-footer">
  <div class="wrap">
    <div>
      <ul><li>HOME</li><li>SERVICES</li><li>ABOUT</li><li>OUR TEAM</li><li>BLOG</li><li>CONTACT</li></ul>
      <p class="copy">© 2024 Harborline Ledger Partners. All rights reserved.</p>
    </div>
    <address>48 Harbor View Lane, Suite 200<br>Mystic, CT 06355<br>Tel: 860.555.0142</address>
  </div>
</footer>
</body>
</html>
```